Help our Sugar Loom find our winning design! We're looking for a business card....

We’re a Sugar Loom in NY specializing in custom-made cakes and unique desserts.
Our cakes combine flavor and art, each designed to match customer’s special event and theme.
We’d like a unique business card with a clean design that will combine French chic and artistic look & feel.
We’d like to differentiate ourselves from standard bakeries, please don’t offer cupcake images :-)
Our logo is peach-pink and brown and we’d love to use these colors ( . Another color that can be added is gold - or feel free to suggest!

Target Market(s)

Women, ages 25-55

Industry/Entity Type

Boutique

Contact Information for Business Card

Text on card:
Logo
Sugar Loom by Dana Welch

www.sugarloomsweets.com
hello@sugarloom.com
(516) 555-0147
F – sugarloomnyc
IG - sugarloom_ny

Font styles to use
Sans Serif
Script

Requirements
Must have
• Logo
• Clean look
• French chic and artistic look & feel.
Nice to have
• Damask pattern
Should not have
• Cupcake images

```html
<!DOCTYPE html>
<html lang="en">
<head>
<meta charset="utf-8">
<title>Sugar Loom – Business Card</title>
<link rel="stylesheet" href="https://fonts.googleapis.com/css2?family=Crimson+Text:wght@400&family=Montserrat:wght@500&display=swap">
<style>
  :root {
    --backdrop: #e4e4e4;
    --blush: #dba2a8;
    --blush-deep: #cf8f96;
    --magenta: #e0177f;
    --peach: #e89a8c;
    --peach-line: #e9a394;
    --gold: #c9a233;
    --gold-light: #f1dc86;
    --brown: #3a2a26;
    --white: #ffffff;
    --flourish: #f6e4e4;
  }
  * { box-sizing: border-box; margin: 0; padding: 0; }
  html, body { width: 1200px; height: 852px; overflow: hidden; }
  body {
    background: var(--backdrop);
    position: relative;
    font-family: "Crimson Text", Georgia, serif;
    color: var(--brown);
  }
  .card {
    position: absolute;
    top: 266px;
    width: 540px;
    height: 320px;
    border-radius: 22px;
    overflow: hidden;
    box-shadow: 0 6px 18px rgba(0,0,0,.18);
  }

  /* Front */
  .card--front { left: 40px; }
  .front-pattern {
    position: absolute; inset: 0;
    background: linear-gradient(135deg, var(--blush) 0%, var(--blush-deep) 100%);
  }
  .front-band {
    position: absolute; left: 0; right: 0; top: 128px; height: 64px;
    background: var(--magenta);
    border-top: 2px solid rgba(255,255,255,.55);
    border-bottom: 2px solid rgba(255,255,255,.55);
  }
  .plaque {
    position: absolute; left: 120px; top: 70px; width: 300px; height: 180px;
    background: var(--white);
    border: 2px solid var(--peach-line);
    border-radius: 60px;
    box-shadow: 0 2px 6px rgba(0,0,0,.15);
  }

  .brand {
    position: absolute; left: 0; right: 0;
    text-align: center;
  }
  .brand__name {
    font-size: 40px;
    line-height: 1;
    color: var(--brown);
  }
  .brand__tagline {
    margin-top: 10px;
    font-family: "Montserrat", Arial, sans-serif;
    font-weight: 500;
    font-size: 10px;
    letter-spacing: 2.6px;
    color: var(--brown);
  }
  .plaque .brand { top: 58px; }

  /* Back */
  .card--back { left: 620px; background: var(--white); }
  .flourish {
    position: absolute;
    background: radial-gradient(ellipse at center, var(--flourish) 0%, rgba(246,228,228,0) 70%);
  }
  .flourish--left { left: 0; top: 120px; width: 120px; height: 110px; }
  .flourish--right { right: 0; top: 0; width: 200px; height: 110px; }
  .back-frame {
    position: absolute; left: 130px; top: 30px; width: 280px; height: 140px;
    border: 2px solid var(--peach-line);
    border-radius: 56px;
  }
  .back-frame .brand { top: 40px; }

  .gold-rule {
    position: absolute; left: 0; right: 0; top: 192px; height: 5px;
    background: linear-gradient(90deg, var(--gold), var(--gold-light), var(--gold));
  }
  .contact-panel {
    position: absolute; left: 0; right: 0; top: 197px; bottom: 0;
    background: var(--peach);
  }
  .contact-list, .social-list {
    position: absolute; list-style: none;
    font-size: 15px; line-height: 21px; color: var(--brown);
  }
  .contact-list { left: 30px; top: 36px; }
  .social-list { right: 30px; top: 16px; }
  .contact-list li, .social-list li { display: flex; align-items: center; gap: 10px; }
  .icon { width: 12px; height: 12px; flex: none; }
  .social-mark {
    width: 11px; height: 11px; flex: none;
    background: var(--brown); border-radius: 2px;
  }
</style>
</head>
<body>

  <section class="card card--front" aria-label="Business card front">
    <div class="front-pattern" role="img" aria-label="Tone-on-tone damask pattern in blush pink"></div>
    <div class="front-band"></div>
    <div class="plaque">
      <div class="brand">
        <p class="brand__name">Sugar Loom</p>
        <p class="brand__tagline">HANDCRAFTED WITH LOVE</p>
      </div>
    </div>
  </section>

  <section class="card card--back" aria-label="Business card back">
    <div class="flourish flourish--left" role="img" aria-label="Faint pink floral flourish"></div>
    <div class="flourish flourish--right" role="img" aria-label="Faint pink floral flourish"></div>
    <div class="back-frame">
      <div class="brand">
        <p class="brand__name">Sugar Loom</p>
        <p class="brand__tagline">HANDCRAFTED WITH LOVE</p>
      </div>
    </div>
    <div class="gold-rule"></div>
    <div class="contact-panel">
      <ul class="contact-list">
        <li>
          <svg class="icon" viewBox="0 0 12 12" aria-hidden="true"><path d="M2.5 1 L4.5 1 L5 3.5 L3.8 4.4 Q4.8 6.8 7.6 8.2 L8.5 7 L11 7.5 L11 9.5 Q10.5 11 9 11 Q1 10 1 2.5 Q1 1 2.5 1 Z" fill="#3a2a26"/></svg>
          (516) 555-0147
        </li>
        <li>
          <svg class="icon" viewBox="0 0 12 12" aria-hidden="true"><circle cx="6" cy="6" r="5" fill="none" stroke="#3a2a26" stroke-width="1.2"/><path d="M1 6 H11 M6 1 Q3 6 6 11 M6 1 Q9 6 6 11" fill="none" stroke="#3a2a26" stroke-width="1"/></svg>
          www.sugarloomsweets.com
        </li>
        <li>
          <svg class="icon" viewBox="0 0 12 12" aria-hidden="true"><rect x="1" y="2.5" width="10" height="7" fill="none" stroke="#3a2a26" stroke-width="1.2"/><path d="M1 2.5 L6 6.5 L11 2.5" fill="none" stroke="#3a2a26" stroke-width="1.2"/></svg>
          hello@sugarloom.com
        </li>
      </ul>
      <ul class="social-list">
        <li><span class="social-mark"></span>sugarloomnyc</li>
        <li><span class="social-mark"></span>sugarloom_ny</li>
      </ul>
    </div>
  </section>

</body>
</html>
```